Unique poster to present as a Gift

I want a simple poster that uses the miniaturised words of Desmond Fairlow's famous poem "Ev" to form the name of my cousin who is receiving Holy Communion. His name is "Tobin". The poster/print would be approxiamately A3 in size, white background with the writing in a dark blue font. The font chosen to write "Tobin" (containing the poem) should be strong and masculine, not a childish font.

```html
<!DOCTYPE html>
<html lang="en">
<head>
<meta charset="utf-8">
<title>Ev — Tobin Communion Poster</title>
<link rel="stylesheet" href="https://fonts.googleapis.com/css2?family=Archivo+Black&family=Bebas+Neue&family=Libre+Baskerville:ital,wght@0,400;0,700;1,400&family=Montserrat:ital,wght@0,500;0,700;0,800;1,800&family=Oswald:wght@500;600&display=swap">
<style>
  :root {
    --frame: #0c2555;
    --ink: #13275a;
    --paper: #ffffff;
    --photo-light: #e8c58f;
    --photo-mid: #b27a3c;
    --photo-dark: #5a3417;
  }
  * { margin: 0; padding: 0; box-sizing: border-box; }
  html, body { width: 1200px; height: 849px; overflow: hidden; background: var(--frame); }
  .poster { position: relative; width: 1200px; height: 849px; background: var(--frame); }
  .sheet { position: absolute; left: 20px; top: 20px; right: 20px; bottom: 21px; background: var(--paper); }
  .initial { position: absolute; left: 40px; top: 228px; }
  .poem { position: absolute; inset: 0; color: var(--ink); }
  .w { position: absolute; white-space: nowrap; line-height: 1; }
  .cond  { font-family: "Oswald", sans-serif; font-weight: 600; text-transform: uppercase; }
  .bebas { font-family: "Bebas Neue", sans-serif; }
  .serif { font-family: "Libre Baskerville", serif; }
  .serif-b { font-family: "Libre Baskerville", serif; font-weight: 700; }
  .sans  { font-family: "Montserrat", sans-serif; font-weight: 500; }
  .sans-b { font-family: "Montserrat", sans-serif; font-weight: 800; }
  .sans-i { font-family: "Montserrat", sans-serif; font-weight: 800; font-style: italic; }
  .black { font-family: "Archivo Black", sans-serif; }
</style>
</head>
<body>
<main class="poster">
  <div class="sheet"></div>

  <svg class="initial" width="220" height="398" viewBox="0 0 220 398" role="img" aria-label="Large letter T filled with a warm photograph of a communion chalice and wheat">
    <defs>
      <linearGradient id="letterPhoto" x1="0" y1="0" x2="1" y2="1">
        <stop offset="0" stop-color="#5a3417"/>
        <stop offset="0.45" stop-color="#e8c58f"/>
        <stop offset="1" stop-color="#b27a3c"/>
      </linearGradient>
    </defs>
    <path d="M0 0 H218 V74 H148 V398 H72 V74 H0 Z" fill="url(#letterPhoto)"/>
  </svg>

  <section class="poem" aria-label="Ev by Desmond Fairlow">
    <!-- letter O -->
    <span class="w cond" style="left:278px;top:230px;font-size:14px">Ev you can stand</span>
    <span class="w cond" style="left:418px;top:230px;font-size:14px">Your ground</span>
    <span class="w serif" style="left:278px;top:252px;font-size:23px">WHEN</span>
    <span class="w serif" style="left:418px;top:252px;font-size:23px">THE</span>
    <span class="w serif" style="left:278px;top:281px;font-size:23px">WINDS</span>
    <span class="w serif" style="left:418px;top:281px;font-size:23px">RISE</span>
    <span class="w sans-b" style="left:278px;top:304px;font-size:15px">ARE HOWLING</span>
    <span class="w sans-b" style="left:418px;top:304px;font-size:15px">LOUD</span>
    <span class="w sans" style="left:278px;top:322px;font-size:15px">and pulling at</span>
    <span class="w sans" style="left:418px;top:322px;font-size:15px">your coat,</span>
    <span class="w bebas" style="left:278px;top:344px;font-size:22px">EV YOU</span>
    <span class="w bebas" style="left:343px;top:344px;font-size:22px">CAN</span>
    <span class="w bebas" style="left:418px;top:344px;font-size:22px">HOLD</span>
    <span class="w sans-b" style="left:278px;top:373px;font-size:12px">STEADY</span>
    <span class="w sans-b" style="left:418px;top:373px;font-size:12px">WHILE</span>
    <span class="w sans-b" style="left:278px;top:391px;font-size:14px">ALL ELSE</span>
    <span class="w black" style="left:352px;top:391px;font-size:14px">SWAYS</span>
    <span class="w sans-b" style="left:418px;top:391px;font-size:14px">LOW,</span>
    <span class="w sans" style="left:278px;top:411px;font-size:18px">AND</span>
    <span class="w sans" style="left:355px;top:411px;font-size:18px">LEND</span>
    <span class="w cond" style="left:418px;top:413px;font-size:14px">A HAND</span>
    <span class="w serif-b" style="left:278px;top:433px;font-size:14px">to those</span>
    <span class="w serif" style="left:358px;top:435px;font-size:12px">falling</span>
    <span class="w serif-b" style="left:418px;top:433px;font-size:14px">down;</span>
    <span class="w sans-b" style="left:278px;top:451px;font-size:14px">EV YOU</span>
    <span class="w sans-b" style="left:366px;top:451px;font-size:14px">CAN</span>
    <span class="w sans-b" style="left:418px;top:451px;font-size:14px">REST</span>
    <span class="w sans-b" style="left:278px;top:470px;font-size:14px">AND</span>
    <span class="w sans-b" style="left:371px;top:470px;font-size:14px">NOT</span>
    <span class="w sans-b" style="left:418px;top:470px;font-size:14px">GO</span>
    <span class="w sans-b" style="left:278px;top:489px;font-size:14px">IDLE</span>
    <span class="w sans-b" style="left:376px;top:489px;font-size:14px">IN RESTING,</span>
    <span class="w cond" style="left:278px;top:510px;font-size:15px">OR BEING</span>
    <span class="w cond" style="left:382px;top:510px;font-size:15px">PASSED OVER,</span>
    <span class="w cond" style="left:278px;top:532px;font-size:15px">DON'T</span>
    <span class="w cond" style="left:388px;top:532px;font-size:15px">GROW BITTER,</span>
    <span class="w sans" style="left:278px;top:553px;font-size:13px">OR</span>
    <span class="w sans" style="left:393px;top:553px;font-size:13px">BEING</span>
    <span class="w sans" style="left:278px;top:569px;font-size:13px">MOCKED,</span>
    <span class="w sans-b" style="left:397px;top:569px;font-size:12px">DON'T GIVE</span>
    <span class="w sans-b" style="left:278px;top:584px;font-size:12px">WAY TO</span>
    <span class="w sans-b" style="left:401px;top:584px;font-size:12px">MOCKING,</span>
    <span class="w cond" style="left:278px;top:600px;font-size:9px">AND YET DON'T</span>
    <span class="w sans" style="left:404px;top:600px;font-size:10px">SEEM TOO PROUD,</span>
    <span class="w sans-b" style="left:278px;top:614px;font-size:11px">NOR SPEAK</span>
    <span class="w sans-b" style="left:408px;top:614px;font-size:11px">TOO LOUD:</span>

    <!-- letter B -->
    <span class="w serif" style="left:590px;top:222px;font-size:22px">EV</span>
    <span class="w serif" style="left:538px;top:247px;font-size:14px">YOU CAN WONDER</span>
    <span class="w sans-b" style="left:520px;top:265px;font-size:9px">- AND NOT LET WONDER LEAD YOU;</span>
    <span class="w sans-i" style="left:516px;top:281px;font-size:12px">Ev you can</span>
    <span class="w sans-i" style="left:628px;top:279px;font-size:14px">plan -</span>
    <span class="w sans-i" style="left:512px;top:296px;font-size:12px">and not</span>
    <span class="w sans-i" style="left:634px;top:296px;font-size:11px">let</span>
    <span class="w serif" style="left:508px;top:310px;font-size:10px">PLANS</span>
    <span class="w sans-i" style="left:634px;top:310px;font-size:10px">RULE YOU;</span>
    <span class="w serif" style="left:508px;top:324px;font-size:10px">EV YOU CAN</span>
    <span class="w serif" style="left:634px;top:323px;font-size:12px">GREET</span>
    <span class="w serif" style="left:508px;top:338px;font-size:10px">BOTH</span>
    <span class="w serif" style="left:634px;top:337px;font-size:12px">PRAISE</span>
    <span class="w serif" style="left:508px;top:352px;font-size:10px">AND</span>
    <span class="w serif" style="left:634px;top:351px;font-size:12px">HARDSHIP</span>
    <span class="w sans-i" style="left:508px;top:365px;font-size:12px">AND</span>
    <span class="w sans-i" style="left:508px;top:380px;font-size:12px">WELCOME</span>
    <span class="w sans-i" style="left:508px;top:394px;font-size:12px">THOSE</span>
    <span class="w sans-i" style="left:508px;top:408px;font-size:12px">TWO</span>
    <span class="w sans-i" style="left:612px;top:408px;font-size:12px">GUESTS</span>
    <span class="w sans-i" style="left:508px;top:427px;font-size:12px">WITH EQUAL</span>
    <span class="w sans-i" style="left:618px;top:427px;font-size:12px">CALM;</span>
    <span class="w cond" style="left:508px;top:455px;font-size:9px">EV YOU CAN</span>
    <span class="w serif" style="left:634px;top:446px;font-size:21px">FACE</span>
    <span class="w sans" style="left:508px;top:468px;font-size:12px">TO SEE</span>
    <span class="w sans" style="left:634px;top:469px;font-size:11px">THE WORK</span>
    <span class="w sans" style="left:508px;top:484px;font-size:13px">YOU'VE</span>
    <span class="w sans" style="left:634px;top:484px;font-size:13px">BUILT</span>
    <span class="w sans" style="left:508px;top:500px;font-size:13px">UNDONE</span>
    <span class="w sans" style="left:634px;top:500px;font-size:11px">BY STORMS</span>
    <span class="w cond" style="left:508px;top:518px;font-size:9px">AND WASHED AWAY</span>
    <span class="w sans" style="left:634px;top:517px;font-size:11px">IN FLOODS,</span>
    <span class="w bebas" style="left:508px;top:534px;font-size:18px">OR FIND</span>
    <span class="w bebas" style="left:634px;top:534px;font-size:18px">THE PLANS</span>
    <span class="w sans" style="left:511px;top:555px;font-size:12px">YOU GAVE</span>
    <span class="w sans" style="left:634px;top:557px;font-size:9px">YOUR HEART TO,</span>
    <span class="w sans-b" style="left:515px;top:570px;font-size:10px">SCATTERED,</span>
    <span class="w cond" style="left:526px;top:587px;font-size:10px">AND KNEEL AND RAISE THEM UP WITH</span>
    <span class="w serif-b" style="left:574px;top:603px;font-size:11px">WEARY</span>
    <span class="w serif-b" style="left:577px;top:618px;font-size:11px">HANDS:</span>

    <!-- letter I -->
    <span class="w bebas" style="left:735px;top:228px;font-size:19px">EV YOU CAN</span>
    <span class="w cond" style="left:861px;top:231px;font-size:13px">GATHER UP</span>
    <span class="w serif-b" style="left:735px;top:248px;font-size:12px">all you hold</span>
    <span class="w cond" style="left:861px;top:249px;font-size:10px">YOUR TREASURES</span>
    <span class="w black" style="left:735px;top:263px;font-size:12px">AND</span>
    <span class="w black" style="left:861px;top:263px;font-size:12px">STAKE IT</span>
    <span class="w serif" style="left:735px;top:279px;font-size:14px">ON ONE</span>
    <span class="w serif" style="left:861px;top:279px;font-size:14px">CAST</span>
    <span class="w serif" style="left:735px;top:296px;font-size:12px">of DICE</span>
    <span class="w serif" style="left:861px;top:296px;font-size:11px">AT DUSK,</span>
    <span class="w serif-b" style="left:735px;top:313px;font-size:17px">And</span>
    <span class="w serif-b" style="left:861px;top:313px;font-size:17px">FAIL,</span>
    <span class="w serif-b" style="left:735px;top:339px;font-size:12px">and BEGIN</span>
    <span class="w serif-b" style="left:861px;top:336px;font-size:16px">anew</span>
    <span class="w serif-b" style="left:735px;top:360px;font-size:13px">FROM THE</span>
    <span class="w black" style="left:861px;top:361px;font-size:12px">FIRST STEP</span>
    <span class="w sans" style="left:735px;top:379px;font-size:13px">And never</span>
    <span class="w sans" style="left:861px;top:379px;font-size:14px">UTTER</span>
    <span class="w black" style="left:735px;top:397px;font-size:15px">a SIGH</span>
    <span class="w sans" style="left:861px;top:396px;font-size:17px">about</span>
    <span class="w bebas" style="left:735px;top:423px;font-size:33px">YOUR</span>
    <span class="w bebas" style="left:861px;top:423px;font-size:33px">FALL;</span>
    <span class="w serif-b" style="left:735px;top:462px;font-size:15px">EV YOU</span>
    <span class="w bebas" style="left:861px;top:455px;font-size:27px">CAN</span>
    <span class="w serif" style="left:735px;top:481px;font-size:12px">urge your</span>
    <span class="w serif" style="left:861px;top:482px;font-size:10px">BODY AND</span>
    <span class="w serif" style="left:735px;top:502px;font-size:10px">BONE AND</span>
    <span class="w serif" style="left:861px;top:497px;font-size:17px">MUSCLE</span>
    <span class="w bebas" style="left:735px;top:516px;font-size:15px">TO CARRY</span>
    <span class="w serif" style="left:861px;top:517px;font-size:12px">YOUR LOAD</span>
    <span class="w bebas" style="left:735px;top:536px;font-size:13px">LONG AFTER</span>
    <span class="w cond" style="left:861px;top:538px;font-size:9px">THEY ARE SPENT,</span>
    <span class="w sans" style="left:738px;top:554px;font-size:13px">And so</span>
    <span class="w serif" style="left:861px;top:555px;font-size:12px">KEEP ON</span>
    <span class="w sans" style="left:742px;top:571px;font-size:9px">WHEN THERE IS</span>
    <span class="w serif" style="left:856px;top:572px;font-size:8px">NOTHING LEFT</span>
    <span class="w sans-b" style="left:756px;top:585px;font-size:12px">EXCEPT THE FAITH WHICH</span>
    <span class="w sans-b" style="left:772px;top:602px;font-size:12px">WHISPERS TO THEM:</span>
    <span class="w sans-b" style="left:802px;top:619px;font-size:9px">'KEEP ON!'</span>

    <!-- letter N -->
    <span class="w serif" style="left:1030px;top:226px;font-size:12px"><b>EV</b> YOU</span>
    <span class="w serif" style="left:998px;top:240px;font-size:12px">CAN WALK AMONG</span>
    <span class="w serif" style="left:984px;top:255px;font-size:12px">CROWDS AND KEEP</span>
    <span class="w serif" style="left:972px;top:270px;font-size:12px">YOUR KINDNESS,</span>
    <span class="w sans-b" style="left:966px;top:285px;font-size:10px">' OR SIT</span>
    <span class="w sans-b" style="left:1082px;top:285px;font-size:10px">WITH LORDS</span>
    <span class="w sans-b" style="left:966px;top:299px;font-size:10px">- NOR LOSE</span>
    <span class="w sans-b" style="left:1086px;top:300px;font-size:8px">THE HUMBLE</span>
    <span class="w sans-b" style="left:962px;top:315px;font-size:9px">HEART,</span>
    <span class="w cond" style="left:962px;top:328px;font-size:10px">EV NEITHER RIVALS</span>
    <span class="w cond" style="left:965px;top:343px;font-size:10px">NOR DEAREST</span>
    <span class="w cond" style="left:968px;top:357px;font-size:10px">FRIENDS CAN</span>
    <span class="w cond" style="left:974px;top:371px;font-size:10px">SWAY YOU,</span>
    <span class="w sans-b" style="left:984px;top:386px;font-size:11px">EV ALL FOLK</span>
    <span class="w sans-b" style="left:996px;top:401px;font-size:11px">LEAN</span>
    <span class="w sans-b" style="left:1007px;top:415px;font-size:11px">ON YOU,</span>
    <span class="w serif" style="left:1020px;top:431px;font-size:9px">but none too</span>
    <span class="w serif" style="left:1035px;top:444px;font-size:9px">hard;</span>
    <span class="w sans-b" style="left:1050px;top:457px;font-size:10px">EV YOU CAN USE</span>
    <span class="w cond" style="left:1062px;top:472px;font-size:10px">THE UNRETURNING</span>
    <span class="w sans-i" style="left:1080px;top:489px;font-size:9px">hour with</span>
    <span class="w sans-b" style="left:1078px;top:503px;font-size:9px">SIXTY MINUTES'</span>
    <span class="w cond" style="left:974px;top:523px;font-size:12px">WORTH OF</span>
    <span class="w bebas" style="left:1084px;top:519px;font-size:18px">GOOD WORK</span>
    <span class="w cond" style="left:976px;top:541px;font-size:14px">DONE,</span>
    <span class="w serif" style="left:964px;top:559px;font-size:11px">Yours is the</span>
    <span class="w serif" style="left:1081px;top:559px;font-size:11px">world and</span>
    <span class="w serif" style="left:976px;top:574px;font-size:11px">all the</span>
    <span class="w serif" style="left:1066px;top:574px;font-size:11px">joy within it,</span>
    <span class="w sans" style="left:1004px;top:589px;font-size:11px">And - BETTER STILL -</span>
    <span class="w sans-b" style="left:1004px;top:603px;font-size:11px">YOU'LL STAND TALL,</span>
    <span class="w sans-b" style="left:1036px;top:618px;font-size:11px">MY BOY!</span>
  </section>
</main>
</body>
</html>
```